Building company buisness cards

We are looking for a sharp modern new look for our business cards.We are a New Zealand based company that specialises in house and land packages.We have attached a photo of the current logo and would like to see if it can be improved somehow if needed.We are open to any colours but we have chosen Black and White at this stage. Feel free to change the font and make the logo smarter looking.Play with the colours and see what looks best.We want a card that looks so good know one will want to throw it away!

Target Market(s)

Building profesonals, home buyers

Industry/Entity Type

Building

Contact Information for Business Card

Garrick Tenwood
0275390628
garrickt@hartvale.co.nz

Font styles to use
Serif
Sans Serif

Colors

Designer to choose colors to be used in the design.

Requirements
Must have
• Just the logo on one side and details on the other
• Clean simple looking card
Nice to have
• Round corners and detail like raised or spot UV
• Something that stands out
Should not have
• To title needed, Director etc

```html
<!DOCTYPE html>
<html lang="en">
<head>
<meta charset="utf-8">
<title>Hartvale Business Cards</title>
<link rel="stylesheet" href="https://fonts.googleapis.com/css2?family=Montserrat:wght@300;400;700&display=swap">
<style>
  :root {
    --backdrop: #1d1d1d;
    --card: #ffffff;
    --ink: #1a1a1a;
    --muted: #8a8a8a;
    --accent: #1f5f9e;
    --divider: #c9c9c9;
  }
  * { box-sizing: border-box; margin: 0; padding: 0; }
  html, body {
    width: 1200px;
    height: 900px;
    overflow: hidden;
    background: var(--backdrop);
    font-family: "Montserrat", sans-serif;
    color: var(--ink);
  }
  .stage { position: relative; width: 1200px; height: 900px; }

  .card {
    position: absolute;
    width: 560px;
    height: 320px;
    background: var(--card);
    border-radius: 22px;
    display: flex;
    align-items: center;
  }
  .card--details { left: 70px; top: 90px; padding-left: 78px; }
  .card--logo { left: 570px; top: 490px; justify-content: center; }

  .wordmark { display: flex; flex-direction: column; }
  .wordmark__name {
    font-weight: 700;
    font-size: 36px;
    letter-spacing: -0.5px;
    color: var(--ink);
    line-height: 1;
  }
  .wordmark__tagline {
    font-weight: 400;
    font-size: 10px;
    color: var(--muted);
    letter-spacing: 0.4px;
    margin-top: 6px;
    padding-left: 2px;
  }
  .card--logo .wordmark__name { font-size: 56px; }
  .card--logo .wordmark__tagline { font-size: 15px; margin-top: 8px; }

  .details { margin-left: 40px; display: flex; flex-direction: column; }
  .details__name-row { display: flex; align-items: center; }
  .details__rule { width: 2px; height: 30px; margin-right: 18px; }
  .details__rule--accent { background: var(--accent); }
  .details__rule--plain { background: var(--divider); height: 44px; margin-right: 22px; }
  .details__name { font-size: 17px; letter-spacing: 0.3px; white-space: nowrap; }
  .details__first { font-weight: 700; }
  .details__last { font-weight: 300; }
  .details__contact-row { display: flex; align-items: center; margin-top: 16px; margin-left: 28px; }
  .contact-list { list-style: none; display: flex; flex-direction: column; gap: 6px; }
  .contact-list__item { display: flex; align-items: center; gap: 7px; font-size: 11px; font-weight: 400; white-space: nowrap; }
  .contact-list__icon { width: 15px; height: 15px; flex: none; }
</style>
</head>
<body>
<main class="stage">
  <section class="card card--details" aria-label="Business card, details side">
    <div class="wordmark">
      <span class="wordmark__name">Hartvale</span>
      <span class="wordmark__tagline">Homes shaped around you.</span>
    </div>
    <div class="details">
      <div class="details__name-row">
        <span class="details__rule details__rule--accent"></span>
        <p class="details__name"><span class="details__first">GARRICK</span> <span class="details__last">TENWOOD</span></p>
      </div>
      <div class="details__contact-row">
        <span class="details__rule details__rule--plain"></span>
        <ul class="contact-list">
          <li class="contact-list__item">
            <svg class="contact-list__icon" viewBox="0 0 16 16" aria-hidden="true">
              <circle cx="8" cy="8" r="8" fill="var(--accent)"/>
              <path d="M5.2 4.2h1.6l.7 1.8-1 .8a5 5 0 0 0 2.7 2.7l.8-1 1.8.7v1.6c0 .5-.4.9-.9.9A6.8 6.8 0 0 1 4.3 5.1c0-.5.4-.9.9-.9z" fill="#fff"/>
            </svg>
            027 539 0628
          </li>
          <li class="contact-list__item">
            <svg class="contact-list__icon" viewBox="0 0 16 16" aria-hidden="true">
              <circle cx="8" cy="8" r="8" fill="var(--accent)"/>
              <rect x="4" y="5.2" width="8" height="5.6" rx="0.6" fill="#fff"/>
              <path d="M4.3 5.5 8 8.4l3.7-2.9" fill="none" stroke="var(--accent)" stroke-width="0.9"/>
            </svg>
            garrickt@hartvale.co.nz
          </li>
        </ul>
      </div>
    </div>
  </section>

  <section class="card card--logo" aria-label="Business card, logo side">
    <div class="wordmark">
      <span class="wordmark__name">Hartvale</span>
      <span class="wordmark__tagline">Homes shaped around you.</span>
    </div>
  </section>
</main>
</body>
</html>
```